Business Card Re-Design/Update

We'd like to update out business cards. I've included our current "Style guide" which has the colour scheme of the organisation in it. I've also included the branding files with logos etc in them.

I've also included a copy of one of our existing cards so that you can see how ugly/dated they look. I'd like a fresh modern corporate look.

Target Market(s)

These are for our clients, potential clients, industry contacts - like all business cards

Contact Information for Business Card

Name
Position
Company Address - Level 1, 47 Fernby Street, Carlow Qld 4072
Direct Phone
mobile
Email
Website -www.korvalit.com.au
Logo

Colors

Designer to choose colors to be used in the design.

Requirements
Must have
• Main Logo
• Cards will need to be editable to be able to personalize them for each new employee.
Nice to have
• The MapOut, ShipWell, KeepSteady would be okay to have if they can be sensibly and professionally added to the look without detracting from the main imagery.
• Maybe they could go on the back of the card? will leave this to your creative discretion as to whether/where they fit.
Should not have
• Should not have decorative or script fonts

```html
<!DOCTYPE html>
<html lang="en">
<head>
<meta charset="utf-8">
<title>Korval IT – Business Card</title>
<link href="https://fonts.googleapis.com/css2?family=Work+Sans:wght@400;500;600&display=swap" rel="stylesheet">
<style>
  :root {
    --backdrop: #2a2a2b;
    --card: #1c1c1d;
    --card-edge: #262627;
    --red: #e0141e;
    --white: #f4f4f4;
    --muted: #e6e6e6;
  }
  * { margin: 0; padding: 0; box-sizing: border-box; }
  html, body {
    width: 1200px; height: 900px; overflow: hidden;
    background: var(--backdrop);
    font-family: "Work Sans", Arial, sans-serif;
  }
  .canvas {
    position: relative; width: 1200px; height: 900px;
  }
  .card {
    position: absolute; left: 290px; width: 620px; height: 380px;
    background: linear-gradient(135deg, var(--card) 0%, var(--card-edge) 100%);
    border-radius: 2px;
  }
  .card--front { top: 40px; }
  .card--back { top: 480px; }

  .brand {
    display: flex; align-items: center; gap: 14px;
  }
  .brand__mark {
    width: 38px; height: 38px; background: var(--red);
  }
  .brand__name {
    color: var(--white); font-weight: 500; letter-spacing: 0.5px;
  }
  .card--front .brand {
    position: absolute; left: 0; right: 0; top: 50%;
    transform: translateY(-50%); justify-content: center;
  }
  .card--front .brand__name { font-size: 52px; }

  .card--back .brand {
    position: absolute; left: 40px; top: 160px;
  }
  .card--back .brand__mark { width: 30px; height: 30px; }
  .card--back .brand__name { font-size: 40px; }

  .divider {
    position: absolute; left: 318px; top: 70px; width: 2px; height: 240px;
    background: var(--red);
  }
  .contact {
    position: absolute; left: 338px; top: 66px; color: var(--muted);
  }
  .contact__name {
    color: var(--red); font-size: 30px; font-weight: 500;
    letter-spacing: 0.5px; line-height: 1;
  }
  .contact__role { font-size: 15px; margin-top: 4px; letter-spacing: 0.4px; }
  .contact__address { font-size: 15px; margin-top: 12px; line-height: 1.3; letter-spacing: 0.4px; }
  .contact__list { list-style: none; margin-top: 12px; }
  .contact__item {
    display: flex; align-items: center; gap: 10px;
    font-size: 15px; line-height: 21px; letter-spacing: 0.4px;
  }
  .contact__icon { width: 11px; height: 11px; flex: none; }
</style>
</head>
<body>
<main class="canvas">
  <section class="card card--front" aria-label="Card front">
    <div class="brand">
      <span class="brand__mark"></span>
      <span class="brand__name">Korval IT</span>
    </div>
  </section>

  <section class="card card--back" aria-label="Card back">
    <div class="brand">
      <span class="brand__mark"></span>
      <span class="brand__name">Korval IT</span>
    </div>
    <div class="divider"></div>
    <div class="contact">
      <p class="contact__name">MAREN ASHBY</p>
      <p class="contact__role">Business Development Manager</p>
      <p class="contact__address">12/58 Calder Bridge Road,<br>Wexley QLD 4011</p>
      <ul class="contact__list">
        <li class="contact__item">
          <svg class="contact__icon" viewBox="0 0 12 12"><rect x="3" y="0.5" width="6" height="11" rx="1" fill="none" stroke="#e0141e" stroke-width="1.2"/><circle cx="6" cy="9.5" r="0.8" fill="#e0141e"/></svg>
          +61 (0)412 555 804
        </li>
        <li class="contact__item">
          <svg class="contact__icon" viewBox="0 0 12 12"><path d="M1 4 Q6 0 11 4 L9.5 5.5 L8 4.5 L4 4.5 L2.5 5.5 Z" fill="#e0141e"/><rect x="2.5" y="6" width="7" height="5" rx="1" fill="#e0141e"/></svg>
          +61 (0)7 3555 2147
        </li>
        <li class="contact__item">
          <svg class="contact__icon" viewBox="0 0 12 12"><path d="M3 1 L5 3.5 L4 5 Q5 7.5 7 8 L8.5 7 L11 9 L9.5 11 Q3 10.5 1 3 Z" fill="#e0141e"/></svg>
          +61 (0)7 3555 2100
        </li>
        <li class="contact__item">
          <svg class="contact__icon" viewBox="0 0 12 12"><rect x="3" y="1" width="6" height="3" fill="#e0141e"/><rect x="1" y="4.5" width="10" height="5" rx="1" fill="#e0141e"/><rect x="3" y="8" width="6" height="3" fill="#e0141e"/></svg>
          +61 (0)7 3555 2199
        </li>
        <li class="contact__item">
          <svg class="contact__icon" viewBox="0 0 12 12"><rect x="0.8" y="2.5" width="10.4" height="7" fill="none" stroke="#e0141e" stroke-width="1.2"/><path d="M1 3 L6 7 L11 3" fill="none" stroke="#e0141e" stroke-width="1.2"/></svg>
          mashby@korvalit.com.au
        </li>
        <li class="contact__item">
          <svg class="contact__icon" viewBox="0 0 12 12"><circle cx="6" cy="6" r="5" fill="none" stroke="#e0141e" stroke-width="1.2"/><ellipse cx="6" cy="6" rx="2.2" ry="5" fill="none" stroke="#e0141e" stroke-width="1"/><line x1="1" y1="6" x2="11" y2="6" stroke="#e0141e" stroke-width="1"/></svg>
          www.korvalit.com.au
        </li>
      </ul>
    </div>
  </section>
</main>
</body>
</html>
```